Easy Marinade Labels for Butchery Store

Need a set of labels designed for a Butchery Shop. They will sit in the top left corner of the packets as a triangle (7cm each side). Easy because the only major requirement is the label name and some small text saying "Please ask in store to see spec sheet for ingredients". Extra points for finding a fun way to incorporate the logo and/or images of food (garlic bulbs, chilli, spices ect) to enhance the label. List of Marinade Names below: GarlicPepper Mint & RosemarySatayBBQChilli Plum & GingerSundried Tomato & BasilBuffaloHoney SoyHoi-SinPer PeriSpicy CajunTeriyakiBlack Bean Ive also attached the logo and an example of how the label might sit on a packet of meat. Thanks

Target Market(s)

Butchery Deli Shop Customers

Industry/Entity Type

Food Store

Font styles to use
Serif
Sans Serif
Decorative
Other font styles liked:
• Fun font that isn't a generic Quellbrix Font?

Colors

Designer to choose colors to be used in the design.

Requirements
Must have
• Product Name
• Small text saying "Please ask in store to see spec sheet for ingredients"
Nice to have
• Photos of ingredients that would match that type of marinade - Chilli, Garlic, Spices.
• Fenly Oak Logo - not essential if it doesn't look good on the label / doesn't fit.

```html
<!DOCTYPE html>
<html lang="en">
<head>
<meta charset="utf-8">
<title>Marinade Label – BBQ Sauce</title>
<link rel="stylesheet" href="https://fonts.googleapis.com/css2?family=Jost:wght@600;700&family=Permanent+Marker&display=swap">
<style>
  :root {
    --page: #ffffff;
    --frame-yellow: #ece51f;
    --label-text: #ffffff;
    --charcoal: #2a2326;
    --ember-red: #b8241c;
    --flame-orange: #f0892a;
    --tomato: #e0532e;
    --garlic: #e9e2d6;
  }
  * { margin: 0; padding: 0; box-sizing: border-box; }
  html, body {
    width: 1200px;
    height: 900px;
    overflow: hidden;
    background: var(--page);
  }
  .canvas {
    position: relative;
    width: 1200px;
    height: 900px;
  }
  .label-shape {
    position: absolute;
    left: 0;
    top: 0;
  }
  .label-copy {
    position: absolute;
    color: var(--label-text);
    text-align: center;
    white-space: nowrap;
  }
  .label-intro {
    left: 523px;
    top: 349px;
    width: 200px;
    font-family: "Jost", sans-serif;
    font-weight: 600;
    font-size: 15px;
    letter-spacing: 2.6px;
  }
  .label-name {
    left: 480px;
    top: 372px;
    width: 270px;
    font-family: "Permanent Marker", cursive;
    font-size: 82px;
    line-height: 82px;
  }
  .label-name span { display: block; }
  .label-notice {
    left: 200px;
    top: 600px;
    width: 844px;
    font-family: "Jost", sans-serif;
    font-weight: 700;
    font-size: 20px;
    letter-spacing: 2.9px;
  }
</style>
</head>
<body>
<main class="canvas">
  <svg class="label-shape" width="1200" height="900" viewBox="0 0 1200 900">
    <defs>
      <linearGradient id="ingredient-tones" x1="0" y1="0" x2="1" y2="0.4">
        <stop offset="0" stop-color="var(--flame-orange)"/>
        <stop offset="0.22" stop-color="var(--charcoal)"/>
        <stop offset="0.48" stop-color="var(--charcoal)"/>
        <stop offset="0.62" stop-color="var(--ember-red)"/>
        <stop offset="0.8" stop-color="var(--tomato)"/>
        <stop offset="1" stop-color="var(--flame-orange)"/>
      </linearGradient>
      <radialGradient id="garlic-glow" cx="0.56" cy="0.12" r="0.14">
        <stop offset="0" stop-color="var(--garlic)"/>
        <stop offset="1" stop-color="var(--garlic)" stop-opacity="0"/>
      </radialGradient>
    </defs>
    <g role="img" aria-label="Painted collage of garlic cloves, glowing charcoal, a grill fork over flames and fresh tomatoes">
      <polygon points="623,177 150,647 1097,647" fill="url(#ingredient-tones)"/>
      <polygon points="623,177 150,647 1097,647" fill="url(#garlic-glow)"/>
    </g>
    <polygon class="label-frame" points="623,177 150,647 1097,647" fill="none" stroke="var(--frame-yellow)" stroke-width="7" stroke-linejoin="miter"/>
  </svg>

  <p class="label-copy label-intro">MARINATED WITH</p>
  <h1 class="label-copy label-name"><span>BBQ</span><span>SAUCE</span></h1>
  <p class="label-copy label-notice">PLEASE ASK IN STORE TO SEE SPEC SHEET FOR INGREDIENTS</p>
</main>
</body>
</html>
```